Business Cards Design for the electrical wholesaler: clean bold dynamic :)

We need a business card design that would follow our latest brand guidelines. As an electrical wholesaler we want to bring a fresh look and feel into the industry. The design should be clean bold and dynamic. It should come alive with the renewed energy of our green colour. Our grey colour should keep things balanced and complement the notion of maturity and responsibility. We employ Lato as a corporate font however are not bound by this font and we’re open to interpretation here.

Target Market(s)

Electrical contractors

Industry/Entity Type

Business

Contact Information for Business Card

Logo
Name & Surname: Halyna Dorosh
Job Title: Director of Marketing
Email: halya.dorosh@quillmail.example
Cell phone: XXX.XXX.XXXX
Address: 20517 - 87 Ave. Edmonton, AB, Canada. T6K 4N8
Business Phone: 780.555.0184
Website: www.brovix.example

Font styles to use
Other font styles liked:
• Lato

Requirements
Must have
• Logo & website
Nice to have
• Brand elements - some of them you may find in the attached Brand Guidelines (e.g. three lines on the background signifying "W")

```html
<!DOCTYPE html>
<html lang="en">
<head>
<meta charset="utf-8">
<title>Brovix Business Card</title>
<link rel="stylesheet" href="https://fonts.googleapis.com/css2?family=Lato:wght@400;700&family=Roboto:wght@400;500&display=swap">
<style>
  :root {
    --backdrop: #b9b9b9;
    --green: #7ab82a;
    --green-light: #86bd24;
    --green-deep: #5e9f22;
    --grey: #4a4d52;
    --grey-text: #55585c;
    --card-white: #f3f3f3;
    --card-white-edge: #e4e4e4;
    --white: #ffffff;
  }
  * { box-sizing: border-box; margin: 0; padding: 0; }
  html, body { width: 1200px; height: 576px; overflow: hidden; }
  body {
    background: var(--backdrop);
    position: relative;
    font-family: "Roboto", Arial, sans-serif;
  }
  .card {
    position: absolute;
    top: 138px;
    height: 294px;
    border-radius: 11px;
    overflow: hidden;
  }
  .card-front {
    left: 82px;
    width: 484px;
    background: linear-gradient(135deg, var(--green-light) 0%, var(--green-deep) 100%);
  }
  .card-back {
    left: 602px;
    width: 482px;
    background: linear-gradient(135deg, var(--white) 0%, var(--card-white) 55%, var(--card-white-edge) 100%);
  }
  .brand {
    position: absolute;
    display: flex;
    align-items: center;
    font-family: "Lato", Arial, sans-serif;
    font-weight: 700;
    color: var(--grey);
    letter-spacing: -0.5px;
  }
  .brand-dot {
    border-radius: 50%;
    flex: none;
  }
  .card-front .brand {
    left: 0; right: 0; top: 120px;
    justify-content: center;
    gap: 14px;
    font-size: 50px;
    line-height: 1;
  }
  .card-front .brand-dot { width: 40px; height: 40px; background: var(--white); }
  .card-back .brand {
    left: 52px; top: 84px;
    flex-direction: column;
    align-items: flex-start;
    gap: 12px;
    font-size: 48px;
    line-height: 1;
  }
  .card-back .brand-dot { width: 44px; height: 44px; background: var(--green); }
  .contact {
    position: absolute;
    left: 266px;
    top: 80px;
    width: 208px;
  }
  .contact-name {
    font-family: "Lato", Arial, sans-serif;
    font-weight: 700;
    font-size: 20px;
    color: var(--green);
    line-height: 22px;
  }
  .contact-title {
    margin-top: 2px;
    font-size: 12px;
    color: var(--grey-text);
  }
  .contact-lines { margin-top: 22px; list-style: none; }
  .contact-lines li {
    display: flex;
    align-items: center;
    gap: 7px;
    font-size: 11.5px;
    color: var(--grey-text);
    height: 17px;
    white-space: nowrap;
  }
  .contact-lines svg { width: 11px; height: 11px; flex: none; }
  .contact-address {
    margin-top: 8px;
    font-size: 11.5px;
    line-height: 17px;
    color: var(--grey-text);
  }
  .band-grey {
    position: absolute;
    left: 0; bottom: 0;
    width: 250px; height: 10px;
    background: var(--grey);
  }
  .band-green {
    position: absolute;
    right: 0; bottom: 0;
    width: 242px; height: 38px;
    background: var(--green);
    clip-path: polygon(14px 0, 100% 0, 100% 100%, 0 100%);
  }
  .website {
    position: absolute;
    left: 266px; bottom: 12px;
    font-size: 12px;
    color: var(--white);
  }
</style>
</head>
<body>

<section class="card card-front">
  <div class="brand"><span class="brand-dot"></span>brovix</div>
</section>

<section class="card card-back">
  <div class="brand"><span class="brand-dot"></span>brovix</div>

  <div class="contact">
    <p class="contact-name">Halyna Dorosh</p>
    <p class="contact-title">Director of Marketing</p>
    <ul class="contact-lines">
      <li>
        <svg viewBox="0 0 12 12" aria-hidden="true">
          <circle cx="6" cy="6" r="6" fill="#7ab82a"/>
          <path d="M3.6 3.4 L4.8 3.2 L5.3 4.6 L4.6 5.1 Q5.2 6.5 6.9 7.4 L7.4 6.7 L8.8 7.2 L8.6 8.4 Q5 8.8 3.6 3.4Z" fill="#fff"/>
        </svg>
        +1 780-555-0184
      </li>
      <li>
        <svg viewBox="0 0 12 12" aria-hidden="true">
          <circle cx="6" cy="6" r="6" fill="#7ab82a"/>
          <rect x="3" y="4" width="6" height="4.2" fill="#fff"/>
          <path d="M3 4 L6 6.4 L9 4" fill="none" stroke="#7ab82a" stroke-width="0.8"/>
        </svg>
        halya.dorosh@quillmail.example
      </li>
    </ul>
    <p class="contact-address">20517 - 87 Ave. Edmonton,<br>AB, Canada. T6K 4N8</p>
  </div>

  <div class="band-grey"></div>
  <div class="band-green"></div>
  <p class="website">www.brovix.example</p>
</section>

</body>
</html>
```